Personal Chef Needs a Good Web Design

Hi everyone!
My name is Leo, I work as a private chef for last 10 years, traveling all around the world and cooking in private megayacht and villas.
I'm about to settle down in my hometown in Europe for a while. And therefore I need a website that will show my story, pics and recipes, nutritional advices and of course offer a Personal and Private Chef services( working for 4-5 families and bringing delicious food to their house).
My clients are extremely rich folks, but usually are down to earth ones.
I believe, the web site should be focused on attention to:
-VIP person's wife( as she is usually responsible for food for family) and be simple.
-to famous people agents and be on high level.

There will be about 10 different menus and 6 different service offers

--UPDATE--
Logo Design:
+My thoughts are- printed structure of the vegetable or fruit on a white font. Like you slice the buffalo tomato, put it in red paint and print it on the edge of the page. See attached files named logo. Can be any nice structured thing, like tomato, lemon, red cabbage etc.
+Classic logos with chef's hat or knives are good too.
+Need to have the space for me to add the name( the fonts can be provided)

Target Market(s)

Private person. 80% Russian clients.

Industry/Entity Type

Cooking

Coding

Coded - Design and coding required

Number of Pages Required

3 page

Requirements
Must have
• Contact form/ Request back call/ Schedule a free consultation
Nice to have
• The client will need to choose straight ahead from the range of services I offer, like:
• -Private Chef( cooking only for the client)
• -Personal Chef( cooking for around 5 clients, bringing the ready to be heated food to their door)
• -Romantic dinner for two
• -Professional Sommelier service
• -Build your kitchen( offering design, equipment and that will fit your requirements)
• -Other( flowers, waiters, barista, equipment rental)
• So this column should go right after the introduction/aboutme part and will lead to separate pages with how-it-works thing for each.

```html
<!DOCTYPE html>
<html lang="en">
<head>
<meta charset="utf-8">
<title>Leo Chef — Private Chef in Megayacht and Villas</title>
<link rel="stylesheet" href="https://fonts.googleapis.com/css2?family=Nunito+Sans:wght@400;600;700&family=Open+Sans:wght@400;600;700&display=swap">
<style>
:root{
  --accent:#d9964a;
  --ink:#1f1f1f;
  --text:#555;
  --muted:#777;
  --line:#cfcfcf;
  --white:#fff;
  --hero-dark:#2a1a12;
}
*{margin:0;padding:0;box-sizing:border-box}
html,body{width:1200px;height:2449px;overflow:hidden;background:var(--white)}
body{position:relative;font-family:"Open Sans",Arial,sans-serif;color:var(--text)}
.abs{position:absolute}
h1,h2,h3,.site-name,.tagline{font-family:"Nunito Sans",Arial,sans-serif}

/* hero */
.hero{position:absolute;left:0;top:0;width:1200px;height:558px;
  background:radial-gradient(ellipse at 60% 45%,#6b3a22 0%,#3b2216 45%,var(--hero-dark) 100%)}
.hero-photo{position:absolute;inset:0;background:linear-gradient(90deg,rgba(120,30,20,.35),rgba(0,0,0,0) 40%,rgba(0,0,0,0) 60%,rgba(130,40,30,.3))}
.site-name{left:98px;top:31px;color:var(--white);font-size:24px;font-weight:700;letter-spacing:.5px}
.menu-btn{left:1066px;top:29px;width:35px;height:35px;border:2px solid var(--white);border-radius:50%}
.menu-btn span{position:absolute;left:10px;width:11px;height:2px;background:var(--white)}
.hero-title{left:0;width:1200px;top:220px;text-align:center;color:var(--white);font-size:56px;font-weight:600;letter-spacing:1px;line-height:70px}
.tagline{left:0;width:1200px;top:345px;text-align:center;color:var(--white);font-size:31px;font-weight:600}
.dots{left:548px;top:499px;display:flex;gap:8px}
.dots i{width:14px;height:14px;border:2px solid var(--white);border-radius:50%}
.dots i.on{background:var(--accent);border-color:var(--accent)}

/* about */
.about-frame{left:98px;top:615px;width:344px;height:408px;border:1px solid #999;padding:5px}
.about-photo{width:100%;height:100%;background:linear-gradient(180deg,#d9d9d4,#a9a9a2 60%,#6d6d68)}
.section-title{color:var(--ink);font-size:32px;font-weight:600;letter-spacing:.5px}
.about .section-title{left:498px;top:616px}
.body-copy{font-size:12px;line-height:32px;color:var(--text)}
.about-copy{left:502px;top:670px;width:600px}
.about-copy p+p{margin-top:32px}
.btn{display:flex;align-items:center;justify-content:center;font-size:11.5px;font-weight:700;letter-spacing:.5px;color:var(--white)}
.btn-solid{background:var(--accent)}
.about .btn{left:502px;top:984px;width:120px;height:33px}

/* benefits */
.benefits-photo{left:0;top:1081px;width:601px;height:397px;background:linear-gradient(180deg,#c9c9c6 0%,#8d8a85 40%,#6f5a42 70%,#8b3b22 100%)}
.benefits{left:601px;top:1081px;width:599px;height:397px;background:var(--accent);color:var(--white)}
.benefits .section-title{position:absolute;left:65px;top:38px;color:var(--white)}
.benefits-intro{position:absolute;left:67px;top:96px;width:480px;font-size:12px;line-height:26px}
.benefit-list{position:absolute;left:67px;top:163px;list-style:none;font-size:12px}
.benefit-list li{display:flex;align-items:center;gap:12px;height:36px}
.benefit-list svg{width:15px;height:15px;flex:none}
.btn-outline{position:absolute;left:67px;top:324px;width:119px;height:33px;border:1.5px solid var(--white)}

/* how it works */
.how .section-title{left:0;width:1200px;top:1552px;text-align:center}
.how-copy{left:165px;top:1614px;width:870px;text-align:center;font-size:12px;line-height:27px}
.how-copy p+p{margin-top:27px}

/* contact */
.contact-rule{left:0;top:1886px;width:1200px;height:5px;background:var(--accent)}
.contact .section-title{left:0;width:1200px;top:1924px;text-align:center}
.col-title{font-size:15px;font-weight:600;color:var(--ink)}
.field-label{font-size:11.5px;color:var(--muted)}
.field{border:1px solid #bdbdbd;background:var(--white)}
.submit{left:642px;top:2300px;width:86px;height:35px;font-size:13.5px}
.info-icon{width:36px;height:36px;border:1.5px solid #aaa;border-radius:50%;display:flex;align-items:center;justify-content:center}
.info-icon svg{width:16px;height:16px}
.info-text{font-size:12.5px;line-height:22px;color:var(--text)}
.hours{left:808px;top:2262px;font-size:12px;color:var(--text)}
.hours div{display:flex;height:26px;align-items:center}
.hours span:first-child{width:143px}

/* footer */
.footer-rule{left:98px;top:2373px;width:1004px;height:1px;background:var(--line)}
.copyright{left:98px;top:2401px;font-size:11.5px;color:var(--muted)}
.social{left:954px;top:2397px;display:flex;gap:14px}
.social span{width:26px;height:26px;background:#9a9a9a;border-radius:3px}
</style>
</head>
<body>

<header class="hero">
  <div class="hero-photo" role="img" aria-label="Festive dinner table with roast dish, candles and vegetables"></div>
  <div class="abs site-name">LEO CHEF</div>
  <div class="abs menu-btn" aria-label="Menu"><span style="top:11px"></span><span style="top:15.5px"></span><span style="top:20px"></span></div>
  <h1 class="abs hero-title">LEO CHEF</h1>
  <p class="abs tagline">Private Chef in Megayacht and Villas</p>
  <div class="abs dots"><i class="on"></i><i></i><i></i><i></i><i></i></div>
</header>

<section class="about">
  <div class="abs about-frame"><div class="about-photo" role="img" aria-label="Smiling chef in white uniform standing in a kitchen"></div></div>
  <h2 class="abs section-title">PRIVATE CHEF</h2>
  <div class="abs body-copy about-copy">
    <p>At vero eos et accusamus et iusto odio dignissimos ducimus qui blanditiis praesentium voluptatum deleniti at que corrupti quos dolores et quas molestias excepturi.</p>
    <p>Sint occaecati cupiditate non provident, similique sunt in culpa qui officia deserunt mollitia animi, id est laborum et dolorum fuga. Et harum quidem rerum facilis est et expedita distinctio. Nam libero tempore, cum soluta nobis est eligendi optio cumque nihil impedit quo minus id quod maxime placeat facere possimus nis voluptas assumenda est, omnis dolor repellendus. Temporibus autem quibusdam et aut officiis debitis aut rerum necessitatibus saepe eveniet ut et voluptates. Et harum quidem rerum facilis est et expedita distinctio. Nam libero tempore, cum eligendi optio cumque nihil impe.</p>
  </div>
  <a class="abs btn btn-solid">READ MORE &gt;&gt;</a>
</section>

<div class="abs benefits-photo" role="img" aria-label="Chef tossing salad beside fresh vegetables and oil bottles"></div>
<section class="abs benefits">
  <h2 class="section-title">BENEFITS</h2>
  <p class="benefits-intro">At vero eos et accusamus et iusto odio dignissimos ducimus qui blanditiis praesen tium voluptatum deleniti atque corrupti quoscaecati.</p>
  <ul class="benefit-list">
    <li><svg viewBox="0 0 16 16"><circle cx="8" cy="8" r="8" fill="#fff"/><path d="M4.5 8.2l2.3 2.3 4.7-4.8" stroke="#d9964a" stroke-width="2" fill="none"/></svg>Nam libero tempore, cum soluta nobis est eligendi optio ostru</li>
    <li><svg viewBox="0 0 16 16"><circle cx="8" cy="8" r="8" fill="#fff"/><path d="M4.5 8.2l2.3 2.3 4.7-4.8" stroke="#d9964a" stroke-width="2" fill="none"/></svg>Debitis aut rerum necessitatibus saepe eveniet ut et volupsitat</li>
    <li><svg viewBox="0 0 16 16"><circle cx="8" cy="8" r="8" fill="#fff"/><path d="M4.5 8.2l2.3 2.3 4.7-4.8" stroke="#d9964a" stroke-width="2" fill="none"/></svg>Ut aut reiciendis voluptatibus maiores alias consequatur volup</li>
    <li><svg viewBox="0 0 16 16"><circle cx="8" cy="8" r="8" fill="#fff"/><path d="M4.5 8.2l2.3 2.3 4.7-4.8" stroke="#d9964a" stroke-width="2" fill="none"/></svg>Ut enim ad minima veniam, quis nostrum exercitationem uluis</li>
  </ul>
  <a class="btn btn-outline">READ MORE &gt;&gt;</a>
</section>

<section class="how">
  <h2 class="abs section-title">HOW IT WORKS</h2>
  <div class="abs how-copy">
    <p>Our first consultation will be in your home. We will discuss any food preferences you may have, as well as any allergy or dietary needs. At this time we will also discus what kind of meals you like, from meat and potatoes to all organic, vegan and vegetarian meals or international cuisine like Italian or Mexican . If you have concerns about your diet we can work with any restrictions you have.</p>
    <p>On your scheduled cook date. We will prepare your meals in our commercial kitchen and drop them off to you at your convenience. Your meals will be chilled, packaged, labeled and stored in your refrigerator or freezer with easy instructions for heating. Meals can be packaged in single servings or family style. All meals will have special heating instructions which most only require you heating it up in the oven.</p>
  </div>
</section>

<section class="contact">
  <div class="abs contact-rule"></div>
  <h2 class="abs section-title">CONTACT US</h2>

  <h3 class="abs col-title" style="left:98px;top:2006px">CONTACT FORM</h3>
  <label class="abs field-label" style="left:98px;top:2048px">NAME :</label>
  <label class="abs field-label" style="left:417px;top:2048px">PHONE NO :</label>
  <div class="abs field" style="left:100px;top:2077px;width:310px;height:33px"></div>
  <div class="abs field" style="left:418px;top:2077px;width:310px;height:33px"></div>
  <label class="abs field-label" style="left:98px;top:2118px">EMAIL :</label>
  <div class="abs field" style="left:100px;top:2143px;width:628px;height:33px"></div>
  <label class="abs field-label" style="left:98px;top:2184px">MESSAGE :</label>
  <div class="abs field" style="left:100px;top:2209px;width:628px;height:82px"></div>
  <a class="abs btn btn-solid submit">SUBMIT</a>

  <h3 class="abs col-title" style="left:808px;top:2006px">CONTACT INFORMATION</h3>
  <div class="abs info-icon" style="left:810px;top:2052px"><svg viewBox="0 0 16 16"><path d="M8 1.5a4.5 4.5 0 0 0-4.5 4.5c0 3.4 4.5 8.5 4.5 8.5s4.5-5.1 4.5-8.5A4.5 4.5 0 0 0 8 1.5z" fill="none" stroke="#d9964a" stroke-width="1.5"/><circle cx="8" cy="6" r="1.6" fill="#d9964a"/></svg></div>
  <div class="abs info-text" style="left:890px;top:2044px">Street # 200 - 315<br>Harbor Town 44120</div>
  <div class="abs info-icon" style="left:810px;top:2108px"><svg viewBox="0 0 16 16"><rect x="1.5" y="3.5" width="13" height="9" rx="1" fill="#d9964a"/><path d="M1.5 4l6.5 5 6.5-5" stroke="#fff" stroke-width="1.2" fill="none"/></svg></div>
  <div class="abs info-text" style="left:890px;top:2115px">info@leochef.example</div>
  <div class="abs info-icon" style="left:810px;top:2164px"><svg viewBox="0 0 16 16"><path d="M4 1.8l2.2 2.8-1.4 1.6c.8 1.9 2.2 3.3 4.1 4.1l1.6-1.4 2.8 2.2-1.3 2.2C7.3 13.1 2.9 8.7 1.8 4.1z" fill="none" stroke="#d9964a" stroke-width="1.4"/></svg></div>
  <div class="abs info-text" style="left:890px;top:2171px">1 - 555 - 555 - 0148</div>

  <h3 class="abs col-title" style="left:808px;top:2231px">OPENING HOURS</h3>
  <div class="abs hours">
    <div><span>Monday - Wednesday &nbsp;:</span><span>10:00 am - 10:00 pm</span></div>
    <div><span>Thursday &amp; Friday &nbsp;:</span><span>10:00 am - 10:00 pm</span></div>
    <div><span>Saturday &amp; Sunday</span><span>9:00 am - 11:00 pm</span></div>
  </div>
</section>

<footer>
  <div class="abs footer-rule"></div>
  <p class="abs copyright">Copyrights © 2016, Leo Chef . All Rights Reserved.</p>
  <div class="abs social" aria-label="Social links"><span></span><span></span><span></span><span></span></div>
</footer>

</body>
</html>
```